Redesign This Psychology Website

We would like a slight redesign of this successful psychology (relationship counselling) website:

www.TheKelvaleClinic.com.au

We are updating the website, and we'd like a slight refresh of the design and style.

Please keep to very similar colours, and use the same logo. We're looking for around 10 page templates, however the main one is the home page.

Keep in mind, this website already converts quite well, so we want a new, fresh design in keeping with this one. Please don't bother designing something too extremely different.

thanks :)

Target Market(s)

couples who are looking for relationship counselling. Men and women, 25 - 70, across Australia

Industry/Entity Type

Psychology

Number of Pages Required

5+ page

Font styles to use
Sans Serif

Colors
87cfc6
b7a5cd
ec1f27
ffffff
cee9f5

Requirements
Must have
• a similar look to the current design, just looking for a slight refresh.
• Search bar
• Areas for lots of photos
• same logo
• lots of content areas
Nice to have
• great content areas, where we can display a lot of content and our areas.
Should not have
• no colors like orange, etc.
• should not have a totally different feel.

```html
<!DOCTYPE html>
<html lang="en">
<head>
<meta charset="utf-8">
<title>Contact Us – The Kelvale Clinic</title>
<link href="https://fonts.googleapis.com/css2?family=Mulish:wght@400;500;600;700&display=swap" rel="stylesheet">
<style>
:root{
  --teal:#87cfc6;
  --teal-mid:#79c7bc;
  --teal-deep:#1f7f86;
  --lilac:#b7a5cd;
  --red:#ec1f27;
  --white:#ffffff;
  --sky:#cee9f5;
  --ink:#2b2b2b;
  --grey:#6b6b6b;
  --grey-light:#f0f0f0;
  --line:#d8d8d8;
}
*{box-sizing:border-box;margin:0;padding:0}
html,body{width:1200px;height:2419px;overflow:hidden}
body{font-family:"Mulish",Arial,sans-serif;color:var(--ink);background:var(--white);position:relative}
.abs{position:absolute}

/* top utility bar */
.utility-bar{left:0;top:0;width:1200px;height:36px;background:var(--grey-light);border-bottom:1px solid var(--line)}
.utility-bar .associate{left:150px;top:9px;font-size:15px;color:#555}
.utility-links{right:135px;top:0;display:flex;height:36px}
.utility-links a{font-size:14px;color:#777;text-decoration:none;padding:0 12px;line-height:36px;border-left:1px solid var(--line)}

/* header */
.brand{display:flex;align-items:center;gap:12px}
.brand-mark{width:44px;height:44px;border-radius:50%;background:var(--teal-deep)}
.brand-name{font-size:30px;font-weight:600;color:var(--teal-deep);letter-spacing:-.3px}
.site-header .brand{left:134px;top:72px}
.search{left:474px;top:84px;width:355px;height:39px;border:1px solid var(--line);border-radius:3px;display:flex;align-items:center;padding-left:10px;gap:8px;font-size:13px;color:#999}
.call{right:132px;top:78px;text-align:right}
.call .label{font-size:16px;color:var(--teal)}
.call .number{font-size:23px;color:var(--teal-deep);font-weight:600;display:flex;align-items:center;gap:6px;justify-content:flex-end}

/* nav */
.main-nav{left:0;top:161px;width:1200px;height:68px;background:linear-gradient(#9fd9d1,var(--teal-mid))}
.main-nav ul{list-style:none;display:flex;position:absolute;left:134px;top:0;height:68px}
.main-nav li{color:var(--white);font-size:17px;font-weight:600;text-align:center;line-height:17px;display:flex;align-items:center;justify-content:center;border-right:1px solid rgba(255,255,255,.45);height:68px}
.main-nav li:last-child{border-right:none}

/* hero */
.hero{left:0;top:229px;width:1200px;height:324px;overflow:hidden;background:linear-gradient(100deg,#d7d3cc 0%,#b9c6cf 40%,#8aa2b6 60%,#c8c8c8 100%)}
.hero-title{left:126px;top:160px;font-size:38px;font-weight:700;color:var(--white);letter-spacing:.5px}
.price-badge{left:650px;top:60px;width:410px;height:410px;border-radius:50%;background:var(--white);border:10px solid rgba(235,235,235,.9);text-align:center;padding-top:52px}
.price-badge h2{font-size:30px;font-weight:500;color:var(--red)}
.price-badge p{font-size:16px;margin-top:8px;line-height:22px}
.price-badge .small{font-size:13px;margin-top:18px;line-height:20px}

/* intro */
.intro{left:135px;top:610px}
.intro h1{font-size:30px;font-weight:500}
.intro .phone{font-size:30px;color:var(--teal-deep);margin-top:8px}
.intro p{font-size:18px;margin-top:2px}

/* forms */
.form-panel{top:757px;width:458px;height:354px;padding:30px 34px;color:var(--white)}
.form-panel.appointment{left:127px;background:var(--teal-mid)}
.form-panel.enquiry{left:610px;background:var(--lilac)}
.form-panel h3{font-size:23px;font-weight:600;margin-bottom:16px}
.field-grid{display:grid;grid-template-columns:192px 192px;column-gap:16px;row-gap:14px}
.field label{display:block;font-size:13px;margin-bottom:6px}
.input{height:32px;background:var(--white)}
.select{height:31px;background:#f1f1f1;color:#777;font-size:12px;display:flex;align-items:center;justify-content:space-between;padding:0 10px}
.radios{font-size:12px;line-height:24px}
.radio{display:flex;align-items:center;gap:6px}
.radio i{width:12px;height:12px;border-radius:50%;background:var(--white);display:inline-block}
.btn-next{margin-top:4px;width:142px;height:37px;background:var(--red);color:var(--white);font-size:17px;font-weight:600;display:flex;align-items:center;justify-content:center}

/* locations */
.locations-title{left:140px;top:1158px;font-size:26px;color:var(--red);font-weight:500}
.location-col{top:1210px;list-style:none}
.location-col li{height:33.7px;font-size:15px;color:#666;display:flex;align-items:center;gap:8px;line-height:15px}
.location-col li::before{content:"";border-left:6px solid var(--teal-mid);border-top:5px solid transparent;border-bottom:5px solid transparent}

/* footer */
.site-footer{left:0;top:2048px;width:1200px;height:299px;background:linear-gradient(#e4e4e4,#fafafa 35%,#f3f3f3)}
.site-footer .brand{left:142px;top:90px}
.footer-col{top:73px}
.footer-col h4{font-size:17px;color:var(--teal-deep);font-weight:600;margin-bottom:10px}
.footer-col li{list-style:none;font-size:13px;color:#555;height:27px}
.socials{display:flex;gap:7px;margin-top:2px}
.socials span{width:31px;height:31px;border-radius:50%}
.copyright{left:0;top:2347px;width:1200px;height:72px;background:var(--grey-light);text-align:center;font-size:12px;color:#666;line-height:72px}
</style>
</head>
<body>

<div class="utility-bar abs">
  <span class="associate abs">Join Our Assoicate Program &rarr;</span>
  <nav class="utility-links abs">
    <a>Home</a><a>Cart</a><a>Blog</a><a>Resources</a><a>Contact</a>
  </nav>
</div>

<header class="site-header">
  <div class="brand abs"><span class="brand-mark"></span><span class="brand-name">The Kelvale Clinic</span></div>
  <div class="search abs">
    <svg width="16" height="16" viewBox="0 0 16 16"><circle cx="6.5" cy="6.5" r="5" fill="none" stroke="#aaa" stroke-width="1.6"/><line x1="10.2" y1="10.2" x2="15" y2="15" stroke="#aaa" stroke-width="1.8"/></svg>
    Search here
  </div>
  <div class="call abs">
    <div class="label">Call Us Now</div>
    <div class="number">
      <svg width="22" height="22" viewBox="0 0 24 24"><path d="M6.6 10.8a15 15 0 0 0 6.6 6.6l2.2-2.2c.3-.3.7-.4 1-.2 1.1.4 2.3.6 3.6.6.6 0 1 .4 1 1V20c0 .6-.4 1-1 1A17 17 0 0 1 3 4c0-.6.4-1 1-1h3.5c.6 0 1 .4 1 1 0 1.3.2 2.5.6 3.6.1.3 0 .7-.2 1z" fill="none" stroke="#ec1f27" stroke-width="1.8"/></svg>
      1300 555 014
    </div>
  </div>
</header>

<nav class="main-nav abs">
  <ul>
    <li style="width:130px">COUNSELLING<br>TYPES</li>
    <li style="width:163px">RELATIONSHIP COUNSELLING<br>LOCATIONS</li>
    <li style="width:135px">SEX THERAPY<br>LOCATIONS</li>
    <li style="width:111px">ABOUT US</li>
    <li style="width:99px">QUIZZES</li>
    <li style="width:120px">FAQ'S</li>
    <li style="width:115px">CONTACT</li>
  </ul>
</nav>

<section class="hero abs" role="img" aria-label="Photo of a smiling couple looking at a laptop together at home">
  <h1 class="hero-title abs">CONTACT US</h1>
  <div class="price-badge abs">
    <h2>Cost of Sessions</h2>
    <p>$160 for 50 min session</p>
    <p>($175 for after hours sessions or all<br>sessions at CBD locations)</p>
    <p class="small">Please enquire for details on Private Health<br>Insurance rebates &amp; Medicare Rebates</p>
  </div>
</section>

<section class="intro abs">
  <h1>The Kelvale Clinic</h1>
  <div class="phone">1300 555 014</div>
  <p>and our friendly receptionists will help you</p>
</section>

<form class="form-panel appointment abs">
  <h3>Request an Appointment</h3>
  <div class="field-grid">
    <div class="field"><label>First Name</label><div class="input"></div></div>
    <div class="field"><label>Last Name</label><div class="input"></div></div>
    <div class="field"><label>Phone</label><div class="input"></div></div>
    <div class="field"><label>Email</label><div class="input"></div></div>
    <div class="field"><label>Type of Counselling</label><div class="select">Relationship Counselling <span>&#9662;</span></div></div>
    <div class="field"><label>I prefer to be contacted by*</label><div class="radios"><div class="radio"><i></i>Email</div><div class="radio"><i></i>Phone</div></div></div>
    <div class="btn-next">Next</div>
  </div>
</form>

<form class="form-panel enquiry abs">
  <h3>Email an Enquiry</h3>
  <div class="field-grid">
    <div class="field"><label>First Name</label><div class="input"></div></div>
    <div class="field"><label>Last Name</label><div class="input"></div></div>
    <div class="field"><label>Phone</label><div class="input"></div></div>
    <div class="field"><label>Email</label><div class="input"></div></div>
    <div class="field"><label>Type of Counselling</label><div class="select">Relationship Counselling <span>&#9662;</span></div></div>
    <div class="field"><label>I prefer to be contacted by*</label><div class="radios"><div class="radio"><i></i>Email</div><div class="radio"><i></i>Phone</div></div></div>
    <div class="btn-next">Next</div>
  </div>
</form>

<h2 class="locations-title abs">Our Location</h2>
<ul class="location-col abs" style="left:132px">
  <li>Adelaide</li><li>Unley</li><li>North Adelaide</li><li>Kensington</li><li>Modbury Heights</li><li>Brisbane</li>
  <li>Brisbane CBD<br>(Wickham Tce &amp; Queen St)</li><li>Carindale</li><li>Indooroopilly</li><li>Annerley</li><li>Auchenflower</li>
  <li>Ashgrove</li><li>Oxley</li><li>Chermside West</li><li>Sunnybank Hills</li><li>Deception Bay</li><li>Canberra</li>
  <li>Phillip</li><li>Hughes</li><li>Cairns</li><li>Cairns CBD</li>
</ul>
<ul class="location-col abs" style="left:381px">
  <li>Central Coast</li><li>Erina</li><li>Gold Coast</li><li>Isle of Capri</li><li>Coomera</li><li>Southport</li><li>Miami</li>
  <li>Mermaid Beach Melbourne</li><li>Berwick</li><li>Tecoma (Belgrave)</li><li>Balwyn</li><li>Carlton Nth</li><li>Nunawading</li>
  <li>East Melbourne</li><li>Altona Meadows</li><li>Moonee Ponds</li><li>Frankston South</li><li>Armadale</li><li>Toorak</li>
  <li>Preston</li><li>Carlton (Marlene)</li>
</ul>
<ul class="location-col abs" style="left:655px">
  <li>Melbourne CBD</li><li>Richmond</li><li>Hampton</li><li>Clifton Hill</li><li>Williamstown</li><li>Perth</li><li>Leeming</li>
  <li>Perth CBD</li><li>West Leederville</li><li>Midland</li><li>Mount Lawley</li><li>Heathridge</li><li>North Perth</li>
  <li>Mandurah</li><li>Ardross</li><li>Subiaco</li><li>Nedlands &nbsp;&nbsp;&nbsp;&nbsp;Sydney</li><li>Randwick</li><li>Five Dock</li>
  <li>Dulwich Hill</li><li>Riverstone</li>
</ul>
<ul class="location-col abs" style="left:887px">
  <li>Green Square (Rosebery)</li><li>Caringbah</li><li>Bondi Junction</li><li>Parramatta</li><li>Mosman</li><li>Penrith</li>
  <li>Sydney CBD (George St)</li><li>Sydney CBD (Pitt St)</li><li>GlebeCrows Nest</li><li>Mona Vale</li><li>Windsor Downs</li>
  <li>Sunshine Coast</li><li>Maroochydore (Corinne)</li><li>Maroochydore (Bronte)</li><li>Townsville</li><li>Rosslea</li>
  <li>Warner's Bay &amp; Newcastle</li><li>(Unavailable at present)</li><li>Wodonga</li><li>Wodonga</li><li>Wollongong</li><li>Wollongong</li>
</ul>

<footer class="site-footer abs">
  <div class="brand abs"><span class="brand-mark"></span><span class="brand-name">The Kelvale Clinic</span></div>
  <div class="footer-col abs" style="left:461px">
    <h4>QUICK LINKS</h4>
    <ul><li>Home</li><li>About Us</li><li>Our Blogs</li><li>Shop Cart</li><li>Contact Us</li></ul>
  </div>
  <div class="footer-col abs" style="left:629px">
    <h4>RESOURCES</h4>
    <ul><li>Counselling Type</li><li>Sex Therapy</li><li>Quizzes</li><li>FAQ</li><li>Relationship Counselling</li></ul>
  </div>
  <div class="footer-col abs" style="left:834px">
    <h4>CONTACT US</h4>
    <ul><li>42 Harbour Lane Suite 12</li><li>1300 555 014</li><li>Email: info@kelvaleclinic.com.au</li></ul>
    <div class="socials">
      <span style="background:#55acee"></span><span style="background:#3b5998"></span><span style="background:#0e76a8"></span><span style="background:#dd4b39"></span>
    </div>
  </div>
</footer>
<div class="copyright abs">&copy; 2017 Company Name &nbsp;All right reserved</div>

</body>
</html>
```